I need a business card for my original fine art pieces

I would like a business card design including a logo design for a new business in the art world. I am based in the Hunter Valley NSW Australia. I am a contemporary figurative, encaustic and wildlife artist. I would like to be able to upload my email and mobile number to this as well. This design should be one that I can incorporate into banners and flyers etc. Id like to incorporate one of my own images or partial image into the background or somewhere below. My initials are RJ and I would like these used as a logo type. I would like the use of some colour and it to be bright and catchy. The final design should communicate artwork custom made and commissions available.

Overview: Original Fine Artworks for sale, online, art galleries etc, Custom made to order and by commission.

Target market is world wide audience and corporate world

My figurative work is painted using acrylics in a lot of natural ochre colours that reflect the Australian Outback, on canvas, linen, paper or board: My encaustic work is created in a contemporary abstract style using a blow torch and a made with a medium of 100% pure bees wax, Damar resin, mixed media and coloured pigments, applied to Birch board. My wildlife are created using coloured pencil and mixed media on a variety of paper types or board.

```html
<!DOCTYPE html>
<html lang="en">
<head>
<meta charset="utf-8">
<title>Rosa Jennings – Business Card</title>
<link href="https://fonts.googleapis.com/css2?family=Cinzel:wght@400;600&family=Open+Sans:wght@400;600&family=Arimo:wght@400&display=swap" rel="stylesheet">
<style>
  :root {
    --bg-top: #c9c9c9;
    --bg-bottom: #fafafa;
    --card-dark: #222222;
    --card-orange: #e8410c;
    --pattern-light: #ee5418;
    --pattern-dark: #e13c08;
    --accent: #ea4a0d;
    --text-light: #e8e8e8;
    --white: #ffffff;
  }
  * { margin: 0; padding: 0; box-sizing: border-box; }
  html, body { width: 1200px; height: 900px; overflow: hidden; }
  body {
    position: relative;
    background: linear-gradient(180deg, var(--bg-top) 0%, #e2e2e2 50%, var(--bg-bottom) 100%);
    font-family: "Open Sans", sans-serif;
  }
  .card {
    position: absolute;
    top: 306px;
    width: 439px;
    height: 271px;
    border-radius: 12px;
    overflow: hidden;
    box-shadow: 0 1px 3px rgba(0,0,0,0.25);
  }
  .card--back { left: 149px; background: var(--card-dark); }
  .card--front { left: 609px; background: var(--card-orange); }

  .brand-ring {
    position: absolute;
    border-radius: 50%;
  }
  .card--back .brand-ring {
    left: 60px; top: 70px;
    width: 84px; height: 84px;
    border: 3px solid var(--accent);
  }
  .card--back .brand-name {
    position: absolute;
    left: 22px; top: 166px; width: 160px;
    text-align: center;
    color: var(--accent);
    font-family: "Open Sans", sans-serif;
    font-weight: 600;
    font-size: 14px;
    line-height: 18px;
  }
  .card--front .brand-ring {
    left: 169px; top: 56px;
    width: 102px; height: 102px;
    border: 3px solid var(--white);
  }

  .contact { position: absolute; left: 232px; top: 57px; color: var(--text-light); }
  .contact__name { color: var(--accent); font-weight: 600; font-size: 17px; line-height: 22px; }
  .contact__role { font-size: 12px; line-height: 15px; margin-left: 4px; }
  .contact__list { list-style: none; margin-top: 15px; font-size: 12px; line-height: 16px; }
  .contact__list li { display: flex; align-items: center; gap: 5px; }
  .contact__list svg { width: 9px; height: 9px; fill: var(--accent); flex: none; }
  .contact__address { margin-top: 13px; font-size: 12px; line-height: 15px; font-style: normal; }

  .pattern-field {
    position: absolute; inset: 0;
    background:
      radial-gradient(ellipse at 30% 25%, rgba(255,120,60,0.35) 0%, rgba(255,120,60,0) 55%),
      radial-gradient(ellipse at 75% 80%, rgba(200,50,0,0.30) 0%, rgba(200,50,0,0) 60%),
      linear-gradient(160deg, var(--pattern-light) 0%, var(--card-orange) 50%, var(--pattern-dark) 100%);
  }
  .wordmark {
    position: absolute; left: 0; right: 0; top: 166px;
    text-align: center; color: var(--white);
  }
  .wordmark__name {
    font-family: "Cinzel", serif; font-weight: 600;
    font-size: 34px; line-height: 38px; letter-spacing: 1px;
  }
  .wordmark__tagline {
    font-family: "Arimo", sans-serif;
    font-size: 15px; line-height: 18px; letter-spacing: 3.4px;
  }
</style>
</head>
<body>
  <section class="card card--back" aria-label="Card back with contact details">
    <div class="brand-ring" aria-hidden="true"></div>
    <p class="brand-name">Rosa Jennings</p>
    <div class="contact">
      <h1 class="contact__name">Daniel Brooks</h1>
      <p class="contact__role">Managing Director</p>
      <ul class="contact__list">
        <li><svg viewBox="0 0 10 10" aria-hidden="true"><path d="M1 3 Q1 1 3 1 H7 Q9 1 9 3 L7 4 L6.5 3 H3.5 L3 4 Z M2.5 5 H7.5 L8.5 9 H1.5 Z"/></svg>555-014-2368</li>
        <li><svg viewBox="0 0 10 10" aria-hidden="true"><path d="M1 2 H9 V8 H1 Z" /><path d="M1 2 L5 5.5 L9 2" fill="none" stroke="#222" stroke-width="1"/></svg>studio@rjfineart.com</li>
        <li><svg viewBox="0 0 10 10" aria-hidden="true"><path d="M4 6 L6 4" stroke="#ea4a0d" stroke-width="1.2"/><rect x="5" y="0.8" width="3" height="5" rx="1.5" transform="rotate(45 6.5 3.3)" fill="none" stroke="#ea4a0d" stroke-width="1.1"/><rect x="2" y="4.2" width="3" height="5" rx="1.5" transform="rotate(45 3.5 6.7)" fill="none" stroke="#ea4a0d" stroke-width="1.1"/></svg>www.rjfineart.com</li>
      </ul>
      <address class="contact__address">1234, Address Goes Here<br>Country Name, 123456</address>
    </div>
  </section>

  <section class="card card--front" aria-label="Card front with name">
    <div class="pattern-field" role="img" aria-label="Faint repeating brand pattern in tones of orange"></div>
    <div class="brand-ring" aria-hidden="true"></div>
    <div class="wordmark">
      <h2 class="wordmark__name">Rosa Jennings</h2>
      <p class="wordmark__tagline">ORIGINAL FINE ARTWORKS</p>
    </div>
  </section>
</body>
</html>
```